Business Card Design for Property Development Company Director

I am looking for a professional and unforgettable business card design for our Director of our Property Development Company.
Please see attached .pptx file to find out what information to include. You don't have to follow the exact format shown in the file - I am interested to see your creative flair using the information provided.

```html
<!DOCTYPE html>
<html lang="en">
<head>
<meta charset="utf-8">
<title>Corvane Property Group – Business Card</title>
<link href="https://fonts.googleapis.com/css2?family=Roboto:wght@400;500;700&family=Roboto+Condensed:wght@700&display=swap" rel="stylesheet">
<style>
  :root {
    --backdrop: #e8e8ea;
    --brand-blue: #274b8e;
    --brand-blue-deep: #1f3f7a;
    --slate: #4a4c50;
    --paper: #f4f4f5;
    --white: #ffffff;
    --muted-white: #dfe6f3;
  }
  * { box-sizing: border-box; margin: 0; padding: 0; }
  html, body {
    width: 1200px; height: 726px; overflow: hidden;
    background: var(--backdrop);
    font-family: "Roboto", Arial, sans-serif;
  }
  .canvas { position: relative; width: 1200px; height: 726px; }

  .card {
    position: absolute; top: 204px;
    width: 520px; height: 318px;
    overflow: hidden;
    box-shadow: 0 8px 22px rgba(0,0,0,0.18);
  }
  .card--front { left: 50px; background: var(--brand-blue); color: var(--white); text-align: center; }
  .card--back { left: 630px; background: var(--brand-blue); }

  /* Front face */
  .front__tagline {
    position: absolute; top: 36px; left: 0; right: 0;
    font-size: 19px; line-height: 1.3; font-weight: 400; color: var(--muted-white);
  }
  .front__brand {
    position: absolute; top: 128px; left: 0; right: 0;
    display: flex; align-items: center; justify-content: center; gap: 16px;
  }
  .brand__square { width: 46px; height: 46px; background: var(--white); }
  .brand__name {
    font-size: 34px; font-weight: 700; letter-spacing: 1px; line-height: 1;
    text-align: left; text-transform: uppercase; color: var(--white);
  }
  .front__invite {
    position: absolute; bottom: 34px; left: 0; right: 0;
    font-size: 16px; font-weight: 400; color: var(--muted-white);
  }

  /* Back face */
  .back__shape { position: absolute; inset: 0; }
  .back__brand {
    position: absolute; left: 0; top: 0; width: 228px; height: 318px;
    display: flex; align-items: center; justify-content: center;
    font-size: 34px; font-weight: 700; color: var(--slate);
    text-transform: uppercase; letter-spacing: 1px;
  }
  .back__details { position: absolute; left: 292px; top: 62px; color: var(--white); }
  .person__name {
    font-family: "Roboto Condensed", Arial, sans-serif;
    font-size: 24px; font-weight: 700; line-height: 1;
  }
  .person__role { font-size: 13px; margin-top: 6px; color: var(--muted-white); }
  .contact { list-style: none; margin-top: 24px; font-size: 14px; line-height: 1.55; }
  .contact li { display: flex; align-items: center; gap: 10px; }
  .contact svg { width: 13px; height: 13px; flex: none; fill: none; stroke: var(--white); stroke-width: 1.6; }
  .contact__licence { margin-top: 4px; font-size: 14px; line-height: 1.35; }
</style>
</head>
<body>
<main class="canvas">

  <section class="card card--front" aria-label="Card front">
    <p class="front__tagline">Property Development<br>&amp; Site Acquisition Specialists</p>
    <div class="front__brand">
      <span class="brand__square" aria-hidden="true"></span>
      <span class="brand__name">Corvane<br>Property Group</span>
    </div>
    <p class="front__invite">Ask me about our INVESTMENT &amp; PARTNERSHIP opportunities</p>
  </section>

  <section class="card card--back" aria-label="Card back">
    <svg class="back__shape" viewBox="0 0 520 318" preserveAspectRatio="none" aria-hidden="true">
      <path d="M0 0 H214 Q280 159 214 318 H0 Z" fill="var(--slate)"/>
      <path d="M0 0 H200 Q266 159 200 318 H0 Z" fill="var(--paper)"/>
    </svg>
    <div class="back__brand">Corvane</div>
    <div class="back__details">
      <h1 class="person__name">Daniel Marsh</h1>
      <p class="person__role">Director</p>
      <ul class="contact">
        <li>
          <svg viewBox="0 0 14 14"><path d="M3 1.5 L5 1.5 L6 4.5 L4.5 5.5 Q5.8 8.3 8.5 9.5 L9.5 8 L12.5 9 L12.5 11 Q12.5 12.5 11 12.5 Q2 12 1.5 3 Q1.5 1.5 3 1.5 Z"/></svg>
          <span>0400 123 456</span>
        </li>
        <li>
          <svg viewBox="0 0 14 14"><rect x="1" y="3" width="12" height="8.5"/><path d="M1 3 L7 8 L13 3"/></svg>
          <span>daniel@corvane.com.au</span>
        </li>
        <li>
          <svg viewBox="0 0 14 14"><circle cx="7" cy="7" r="5.8"/><ellipse cx="7" cy="7" rx="2.6" ry="5.8"/><path d="M1.2 7 H12.8"/></svg>
          <span>www.corvane.com.au</span>
        </li>
      </ul>
      <p class="contact__licence">Real Estate Lic:<br>1234567 &amp; 1234568</p>
    </div>
  </section>

</main>
</body>
</html>
```